Redesign website for small print company

Vindurgata is a small printing company in Iceland mainly servicing Students, schools, etc. We are also doing all kind of other jobs, like business cards, book printing, brochure printing etc. We are also selling books online.
Our website is: www.vindurgata.is
What we are looking for is:
- Web Design (Uncoded - PSD layout only)
- Mobile friendly design, using our current color scheme: Red, green, yellow and light gray.
- Clean simple design
- Simple, light and easy to use.
- More menu Items/drop down
Industry/Entity Type
Digital Printing
Number of Pages Required
5+ page
Requirements
Must have
- Easy navigation
- Designed for mobile
- Current color scheme (see logo)
Nice to have
- Icon based products

```html
<!DOCTYPE html>
<html lang="en">
<head>
<meta charset="utf-8">
<title>Vindurgata – Printing for students and schools</title>
<link href="https://fonts.googleapis.com/css2?family=Lato:wght@400;700;900&family=Roboto:wght@400;500;700&display=swap" rel="stylesheet">
<style>
:root{
  --red:#e3262b;
  --green:#135a2b;
  --green-dark:#0f4a23;
  --yellow:#e6c01a;
  --ink:#1c1c1c;
  --text:#555;
  --muted:#8a8a8a;
  --light:#f3f3f3;
  --footer:#232323;
}
*{margin:0;padding:0;box-sizing:border-box}
html,body{width:1200px;height:3327px;overflow:hidden}
body{position:relative;background:#fff;font-family:"Roboto",Arial,sans-serif;color:var(--text)}
.abs{position:absolute}
h1,h2,h3,.heading{font-family:"Lato",Arial,sans-serif}

/* header */
.top-line{left:0;top:0;width:1200px;height:4px;background:var(--red)}
.brand{left:98px;top:26px;height:50px;display:flex;align-items:center;gap:10px;font-family:"Lato",sans-serif;font-weight:900;font-size:31px;color:var(--ink)}
.brand-square{width:42px;height:42px;background:var(--red)}
.nav{right:100px;top:30px;display:flex;align-items:center;gap:24px;font-family:"Roboto",sans-serif;font-weight:700;font-size:15px;color:var(--ink)}
.nav-icon{width:38px;height:38px;border-radius:50%;display:flex;align-items:center;justify-content:center}
.nav-icon.search{border:1px solid #ccc}
.nav-icon.cart{background:var(--green)}

/* hero */
.hero{left:0;top:100px;width:1200px;height:555px;background:linear-gradient(100deg,#d9a25a 0%,#cfc7b8 35%,#e7e7e3 55%,#9fb2c4 80%,#c99b4c 100%)}
.hero-title{left:586px;top:180px;font-size:54px;font-weight:900;color:var(--ink);letter-spacing:1px}
.hero-sub{left:586px;top:263px;width:520px;font-size:21px;font-weight:700;color:#333;line-height:32px}
.btn{display:flex;align-items:center;justify-content:center;gap:8px;font-family:"Roboto",sans-serif;font-weight:700;color:#fff;text-transform:uppercase}
.hero-btn{left:586px;top:354px;width:175px;height:48px;background:var(--green);font-size:16px}

/* category tiles */
.tiles{left:0;top:655px;width:1200px;height:147px;display:flex}
.tile{width:200px;height:147px;display:flex;flex-direction:column;align-items:center;justify-content:flex-end;padding-bottom:20px;gap:14px;color:#fff;font-weight:700;font-size:17px;font-family:"Roboto",sans-serif}
.tile.red{background:var(--red)}.tile.green{background:var(--green)}.tile.yellow{background:var(--yellow)}

/* page backdrop */
.backdrop{left:0;top:802px;width:1200px;height:1215px;background:linear-gradient(180deg,#f7f7f7,#efefef 50%,#f6f6f6)}
.ghost{font-family:"Lato",sans-serif;font-weight:900;color:rgba(0,0,0,.06);font-size:76px;white-space:nowrap}

/* welcome */
.welcome-title{left:98px;top:912px;font-size:35px;font-weight:700;color:var(--ink)}
.welcome-copy{left:98px;top:985px;width:480px;font-size:14px;line-height:25px;color:var(--text)}
.welcome-copy p{margin-bottom:18px}
.welcome-btn{left:98px;top:1184px;width:160px;height:46px;background:var(--green);font-size:15px}
.video{left:635px;top:925px;width:465px;height:305px;border:4px solid #fff;box-shadow:0 2px 8px rgba(0,0,0,.25);background:linear-gradient(135deg,#b8c2b5,#7f8f86 50%,#3d4846)}
.play{left:834px;top:1058px;width:66px;height:46px;border-radius:12px;background:var(--red);display:flex;align-items:center;justify-content:center}
.divider{left:98px;top:1336px;width:1002px;height:1px;background:#d5d5d5}

/* section headings */
.sec-title{width:1200px;left:0;text-align:center;font-size:34px;font-weight:700;color:var(--ink)}
.sec-text{width:680px;left:260px;text-align:center;font-size:14px;line-height:25px}

/* work cards */
.work{top:1580px;width:228px}
.work-img{width:228px;height:170px;border:3px solid #fff;box-shadow:0 1px 4px rgba(0,0,0,.2)}
.work-body{margin-top:20px;border-left:3px solid var(--red);padding-left:13px}
.work-body h3{font-family:"Roboto",sans-serif;font-size:18px;font-weight:500;color:var(--ink)}
.work-body p{font-size:13px;color:var(--muted);margin-top:6px;white-space:nowrap}
.all-btn{left:495px;top:1865px;width:210px;height:48px;background:var(--yellow);color:var(--ink);font-size:16px}

/* how it works */
.how-band{left:0;top:2017px;width:1200px;height:338px;background:var(--green-dark)}
.how .ghost{color:rgba(255,255,255,.1)}
.step{width:206px;height:206px;border-radius:50%;background:#fff;box-shadow:0 3px 10px rgba(0,0,0,.25);display:flex;flex-direction:column;align-items:center;justify-content:center;gap:10px;font-family:"Roboto",sans-serif;font-weight:500;font-size:19px;color:var(--ink)}

/* books */
.book-cover{top:2630px;width:167px;height:218px;box-shadow:0 2px 6px rgba(0,0,0,.25);background:linear-gradient(180deg,#eef0f2,#a9b6c2)}
.book-info{top:2632px;width:290px}
.book-info h3{font-family:"Roboto",sans-serif;font-weight:400;font-size:26px;color:var(--ink)}
.book-info .author{color:var(--red);font-size:15px;margin-top:8px}
.book-info p{font-size:13px;line-height:22px;color:var(--muted);margin-top:12px}
.buy{width:118px;height:38px;background:var(--green);font-size:14px;margin-top:22px}

/* footer */
.f-photo{left:0;top:2975px;width:400px;height:352px;background:linear-gradient(160deg,#cfe0f0,#5f86ae 45%,#17324f)}
.f-mid{left:400px;top:2975px;width:400px;height:352px;background:var(--footer);color:#fff;text-align:center}
.f-map{left:800px;top:2975px;width:400px;height:352px;background:linear-gradient(135deg,#f1efe6,#e4e1d3)}
.f-mid h4{font-family:"Roboto",sans-serif;font-weight:500;font-size:15px;letter-spacing:.5px}
.f-input{left:58px;top:90px;width:284px;height:36px;border:1px solid #ddd;text-align:left;padding:9px 10px;font-size:12px;color:#fff}
.f-sub{left:135px;top:137px;width:130px;height:38px;background:var(--red);font-size:14px}
.contact-line{width:400px;left:0;display:flex;justify-content:center;align-items:center;gap:10px;font-size:14px}
.up{left:573px;top:2948px;width:54px;height:54px;border-radius:50%;background:#fff;box-shadow:0 2px 6px rgba(0,0,0,.25);display:flex;align-items:center;justify-content:center}
.direction{left:818px;top:2990px;width:136px;height:34px;background:var(--yellow);color:var(--ink);font-size:13px}
</style>
</head>
<body>

<div class="abs top-line"></div>
<header>
  <div class="abs brand"><span class="brand-square"></span>Vindurgata</div>
  <nav class="abs nav">
    <span>HOME</span><span>SERVICES ▾</span><span>SUBMISSION OF WORKS</span><span>ABOUT US</span>
    <span class="nav-icon search"><svg width="16" height="16" viewBox="0 0 16 16"><circle cx="6.5" cy="6.5" r="5" fill="none" stroke="#e3262b" stroke-width="2"/><path d="M10 10l4.5 4.5" stroke="#e3262b" stroke-width="2.4"/></svg></span>
    <span class="nav-icon cart"><svg width="18" height="16" viewBox="0 0 18 16"><path d="M1 2h3l2 8h9l2-6H5" fill="none" stroke="#fff" stroke-width="2"/><circle cx="7" cy="13.5" r="1.6" fill="#fff"/><circle cx="14" cy="13.5" r="1.6" fill="#fff"/></svg></span>
  </nav>
</header>

<section class="hero-block">
  <div class="abs hero" role="img" aria-label="Photo of smiling students walking through a campus hallway carrying notebooks"></div>
  <h1 class="abs hero-title">VINDURGATA</h1>
  <p class="abs hero-sub">Nemo enim ipsam voluptatem quia voluptas aspernatur aut odit aut fugit sed quia magni dolores.</p>
  <a class="abs btn hero-btn">Read more <svg width="16" height="16" viewBox="0 0 16 16"><circle cx="8" cy="8" r="7.5" fill="#fff"/><path d="M5 8h6M8.5 5l3 3-3 3" fill="none" stroke="#135a2b" stroke-width="2"/></svg></a>
</section>

<section class="abs tiles">
  <div class="tile red"><svg width="54" height="62" viewBox="0 0 54 62" fill="none" stroke="#fff" stroke-width="2.5"><path d="M8 4h28l10 10v44H8z"/><path d="M36 4v10h10"/><path d="M17 22h20M17 30h20M17 38h14M17 46h20"/></svg>ESSAYS</div>
  <div class="tile green"><svg width="70" height="62" viewBox="0 0 70 62" fill="none" stroke="#fff" stroke-width="2.5"><path d="M6 30l26-22 32 20-26 24z"/><path d="M14 36l26-22 26 16"/><path d="M24 30l10 6M30 25l10 6"/></svg>BUSINESS CARDS</div>
  <div class="tile yellow"><svg width="74" height="62" viewBox="0 0 74 62" fill="none" stroke="#fff" stroke-width="2.5"><path d="M4 8l22 6 22-6 22 6v42l-22-6-22 6-22-6z"/><path d="M26 14v42M48 8v42"/><path d="M9 22h12M9 30h12M31 22h12M31 30h12M53 22h12M53 30h12"/></svg>PAMPHLETS</div>
  <div class="tile red"><svg width="70" height="62" viewBox="0 0 70 62" fill="none" stroke="#fff" stroke-width="2.5"><path d="M6 14c10-4 20-4 29 2 9-6 19-6 29-2v40c-10-4-20-4-29 2-9-6-19-6-29-2z"/><path d="M35 16v40M12 24h16M12 32h16M42 24h16M42 32h16"/></svg>BOOK PRINTING</div>
  <div class="tile green"><svg width="64" height="62" viewBox="0 0 64 62" fill="none" stroke="#fff" stroke-width="2.5"><rect x="6" y="6" width="52" height="40"/><circle cx="22" cy="22" r="7"/><path d="M34 18h18M34 26h18M14 36h38M32 46v12M20 58l12-12 12 12"/></svg>POSTERS</div>
  <div class="tile yellow"><svg width="60" height="62" viewBox="0 0 60 62" fill="none" stroke="#fff" stroke-width="2.5"><path d="M10 6h36v46H14a4 4 0 0 1-4-4z"/><path d="M10 48a4 4 0 0 1 4-4h32M14 56h32"/><rect x="28" y="2" width="28" height="14" fill="#e6c01a"/><text x="42" y="13" font-size="9" fill="#fff" stroke="none" text-anchor="middle" font-family="Roboto,sans-serif" font-weight="700">TEXT</text></svg>TEXTBOOKS</div>
</section>

<div class="abs backdrop" role="img" aria-label="Soft faded photo of a print shop interior behind the content"></div>

<section class="welcome">
  <div class="abs ghost" style="left:0;top:880px;">ABOUT US</div>
  <h2 class="abs welcome-title">WELCOME TO UNIVERSITY</h2>
  <div class="abs welcome-copy">
    <p>We are located in the campus, which has specialized in the service of school staff, as well as providing general public printing.</p>
    <p>Higher education publishes seminars and first-class textbooks for courses, prints theses for lesson, as well as working on an unprecedented number of smaller pieces for students, teachers and organizations. These include brochures, reports, questionnaires, business cards, books...</p>
  </div>
  <a class="abs btn welcome-btn">Read more <svg width="14" height="14" viewBox="0 0 16 16"><circle cx="8" cy="8" r="7.5" fill="#fff"/><path d="M5 8h6M8.5 5l3 3-3 3" fill="none" stroke="#135a2b" stroke-width="2"/></svg></a>
  <div class="abs video" role="img" aria-label="Video still of a print shop worker handing over a printed order at the counter"></div>
  <div class="abs play"><svg width="20" height="22" viewBox="0 0 20 22"><path d="M2 1l17 10L2 21z" fill="#fff"/></svg></div>
  <div class="abs divider"></div>
</section>

<section class="latest">
  <div class="abs ghost" style="left:0;width:1200px;text-align:center;top:1405px;">LATEST WORK</div>
  <h2 class="abs sec-title" style="top:1432px;">LATEST WORK</h2>
  <p class="abs sec-text" style="top:1500px;">Higher education is a tailored print shop, The Heron is the official eco-label of the Nordic countries, which has created a foothold in this country and is known among consumers.</p>

  <div class="abs work" style="left:98px;"><div class="work-img" role="img" aria-label="Photo of dark and orange business cards" style="background:linear-gradient(160deg,#4a4a4a,#1f1f1f 60%,#c8652a)"></div><div class="work-body"><h3>Business Cards</h3><p>Lorem ipsum dolor sit consectur...</p></div></div>
  <div class="abs work" style="left:356px;"><div class="work-img" role="img" aria-label="Photo of a company profile brochure with blue cover" style="background:linear-gradient(150deg,#e9eef2,#b8cbd9 50%,#2f7fa8)"></div><div class="work-body"><h3>Brochure Printing</h3><p>Lorem ipsum dolor sit consectur...</p></div></div>
  <div class="abs work" style="left:614px;"><div class="work-img" role="img" aria-label="Photo of a colourful stack of printed books" style="background:linear-gradient(180deg,#d8c9a8,#c14b3a 40%,#3a6fb0 70%,#e0b43a)"></div><div class="work-body"><h3>Book Printing</h3><p>Lorem ipsum dolor sit consectur...</p></div></div>
  <div class="abs work" style="left:872px;"><div class="work-img" role="img" aria-label="Photo of a street poster display stand" style="background:linear-gradient(160deg,#cfd6d8,#8a9a8c 50%,#5b6a5c)"></div><div class="work-body"><h3>Posters</h3><p>Lorem ipsum dolor sit consectur...</p></div></div>

  <a class="abs btn all-btn">View all works <svg width="16" height="16" viewBox="0 0 16 16"><circle cx="8" cy="8" r="7" fill="none" stroke="#1c1c1c" stroke-width="1.6"/><path d="M5 8h6M8.5 5l3 3-3 3" fill="none" stroke="#1c1c1c" stroke-width="1.8"/></svg></a>
</section>

<section class="how">
  <div class="abs how-band"></div>
  <div class="abs ghost" style="left:0;width:1200px;text-align:center;top:2060px;">HOW IT WORKS</div>
  <h2 class="abs sec-title" style="top:2085px;color:#fff;">HOW IT WORKS</h2>
  <p class="abs sec-text" style="top:2148px;color:#fff;">Higher education is a tailored print shop, The Heron is the official eco-label of the Nordic countries, which has created a foothold in this country and is known among consumers.</p>
  <svg class="abs" style="left:0;top:2300px" width="1200" height="110" viewBox="0 0 1200 110"><path d="M270 50 C 380 80, 460 80, 600 50 S 820 20, 930 50" fill="none" stroke="#e6c01a" stroke-width="3" stroke-dasharray="6 5"/></svg>
  <div class="abs step" style="left:167px;top:2250px;"><svg width="80" height="72" viewBox="0 0 80 72" fill="none" stroke="#e3262b" stroke-width="2.4"><rect x="6" y="4" width="44" height="52"/><path d="M14 40V28M22 40V20M30 40V24M38 40V14M56 16h16l-4-4M56 28h16l-4-4M56 40h16l-4-4"/><circle cx="32" cy="56" r="10" fill="#fff"/><path d="M27 56l4 4 7-8"/></svg>SENDA VERK</div>
  <div class="abs step" style="left:497px;top:2250px;"><svg width="80" height="72" viewBox="0 0 80 72" fill="none" stroke="#e3262b" stroke-width="2.4"><rect x="6" y="6" width="68" height="44"/><path d="M30 50l-4 14h28l-4-14M20 64h40"/><path d="M26 42l10-26 4 8 6-10 8 28z"/></svg>HANNA VERK</div>
  <div class="abs step" style="left:827px;top:2250px;"><svg width="80" height="72" viewBox="0 0 80 72" fill="none" stroke="#e3262b" stroke-width="2.4"><path d="M18 30l14-14 10 10-14 14zM40 14l12-10 10 10-10 12z"/><path d="M10 40h8l6 20h30l8-16H22"/><circle cx="28" cy="66" r="3"/><circle cx="50" cy="66" r="3"/></svg>FA TILBOD</div>
</section>

<section class="books">
  <div class="abs ghost" style="left:0;width:1200px;text-align:center;top:2500px;">OUR BOOKS</div>
  <h2 class="abs sec-title" style="top:2532px;">OUR BOOKS</h2>

  <div class="abs book-cover" style="left:98px;" role="img" aria-label="Book cover artwork with a city tower photo"></div>
  <div class="abs book-info" style="left:290px;">
    <h3>Book Name</h3><div class="author">Book Author Name</div>
    <p>Duis aute irure dolor in reprehenderit in voluptate velit esse cillum dolore eu fugiat nulla pariatur. Excepteur sint occaecat cupidatat...</p>
    <a class="btn buy">Buy now <svg width="13" height="13" viewBox="0 0 16 16"><circle cx="8" cy="8" r="7.5" fill="#fff"/><path d="M5 8h6M8.5 5l3 3-3 3" fill="none" stroke="#135a2b" stroke-width="2"/></svg></a>
  </div>

  <div class="abs book-cover" style="left:618px;background:linear-gradient(180deg,#eef2f6,#7ea3c8);" role="img" aria-label="Book cover artwork with a city skyline photo"></div>
  <div class="abs book-info" style="left:810px;">
    <h3>Book Name</h3><div class="author">Book Author Name</div>
    <p>Duis aute irure dolor in reprehenderit in voluptate velit esse cillum dolore eu fugiat nulla pariatur. Excepteur sint occaecat cupidatat...</p>
    <a class="btn buy">Buy now <svg width="13" height="13" viewBox="0 0 16 16"><circle cx="8" cy="8" r="7.5" fill="#fff"/><path d="M5 8h6M8.5 5l3 3-3 3" fill="none" stroke="#135a2b" stroke-width="2"/></svg></a>
  </div>
</section>

<footer>
  <div class="abs f-photo" role="img" aria-label="Photo looking up at glass office towers against a bright sky"></div>
  <div class="abs f-mid">
    <h4 class="abs" style="left:0;width:400px;top:50px;">NEWSLETTER SUBSCRIPTION</h4>
    <div class="abs f-input">Email</div>
    <a class="abs btn f-sub">Subscribe</a>
    <h4 class="abs" style="left:0;width:400px;top:200px;">CONTACT US</h4>
    <div class="abs contact-line" style="top:230px;"><svg width="14" height="14" viewBox="0 0 16 16"><path d="M3 1l3 0 1.5 4-2 1.5a9 9 0 0 0 4 4l1.5-2 4 1.5v3l-2 2C7 15 1 9 1 3z" fill="#fff"/></svg>555 0147</div>
    <div class="abs contact-line" style="top:258px;"><svg width="15" height="12" viewBox="0 0 15 12"><rect width="15" height="12" fill="#fff"/><path d="M0 0l7.5 6L15 0" fill="none" stroke="#232323" stroke-width="1.4"/></svg>verk@vindurgata.is</div>
    <div class="abs" style="left:0;width:400px;top:303px;font-size:13px;">© Copyright 2018 Vindurgata. All Rights Reserved.</div>
  </div>
  <div class="abs f-map" role="img" aria-label="Street map showing the shop location"></div>
  <svg class="abs" style="left:992px;top:3120px" width="22" height="30" viewBox="0 0 22 30"><path d="M11 0a11 11 0 0 1 11 11c0 8-11 19-11 19S0 19 0 11A11 11 0 0 1 11 0z" fill="#e3262b"/><circle cx="11" cy="11" r="4" fill="#fff"/></svg>
  <a class="abs btn direction"><svg width="14" height="12" viewBox="0 0 14 12"><path d="M1 11c1-5 4-7 8-7V1l5 4.5L9 10V7C5 7 3 8 1 11z" fill="#1c1c1c"/></svg>Get direction</a>
  <div class="abs up"><svg width="22" height="20" viewBox="0 0 22 20" fill="none" stroke="#1c1c1c" stroke-width="2.6"><path d="M3 10l8-7 8 7M3 18l8-7 8 7"/></svg></div>
</footer>

</body>
</html>
```